Business Card Design Project

I need a business card design for my freelance solo makeup artistry business in Melbourne, Australia called Rosa Vantelli. My freelance business specialises in bridal and special occassions makeup.

I like the idea of having Rosa Vantelli in pink as its a feminine and soft colour. I would like a very clean, classy and simple (with an element of fun if that's possible) design. I would consider the business name to be in gloss with an otherwise matte finish.

Underneath the business name, I would like "Makeup by Tara Quimbley"

I do not want any bridal related graphics.

Target Market(s)

Young females with a disposable income from ages 20-40 and females getting married who will dictate who does mother of bride makeup ages 40-70.

Industry/Entity Type

Business

Requirements
Must have
• "Makeup by Tara Quimbley"

Ph: 0412 538 064
E: rosavantelli@mailzone.example
ABN: 58902174635
Nice to have
• I think I would like a mini business cards which is more slimline. I do like the colours of pink, white and grey but open to suggestions.
Should not have
• Bridal related graphics

```html
<!DOCTYPE html>
<html lang="en">
<head>
<meta charset="utf-8">
<title>Rosa Vantelli – Business Card</title>
<link rel="stylesheet" href="https://fonts.googleapis.com/css2?family=Open+Sans:wght@300;400;500&family=Caveat:wght@500&display=swap">
<style>
  :root {
    --card-bg: #ffffff;
    --frame: #111111;
    --brand-pink: #f27a9c;
    --label-pink: #ffc6d8;
    --band-dark: #1e1e1e;
    --gloss-pink: #f4a3b4;
    --gloss-grey: #e4e4e4;
    --contact-grey: #555555;
  }
  * { margin: 0; padding: 0; box-sizing: border-box; }
  html, body {
    width: 1200px;
    height: 686px;
    overflow: hidden;
    background: var(--card-bg);
  }
  .card {
    position: relative;
    width: 1200px;
    height: 686px;
    background: var(--card-bg);
    font-family: "Open Sans", Arial, sans-serif;
  }
  .card__frame {
    position: absolute;
    left: 30px;
    top: 58px;
    width: 1142px;
    height: 580px;
    border: 7px solid var(--frame);
    border-radius: 42px;
  }
  .gloss-area {
    position: absolute;
    left: 700px;
    top: 100px;
    width: 468px;
    height: 46px;
    background: linear-gradient(90deg, var(--gloss-pink) 0%, var(--gloss-grey) 45%, var(--gloss-grey) 100%);
  }
  .brand-name {
    position: absolute;
    left: 72px;
    top: 136px;
    font-family: "Open Sans", Arial, sans-serif;
    font-weight: 300;
    font-size: 146px;
    line-height: 1;
    color: var(--brand-pink);
    white-space: nowrap;
  }
  .pencil-area {
    position: absolute;
    left: 37px;
    top: 455px;
    width: 913px;
    height: 72px;
    background: var(--band-dark);
  }
  .tagline {
    position: absolute;
    left: 124px;
    top: 466px;
    display: flex;
    align-items: baseline;
    gap: 22px;
    white-space: nowrap;
  }
  .tagline__lead {
    font-family: "Open Sans", Arial, sans-serif;
    font-weight: 500;
    font-size: 28px;
    color: var(--label-pink);
  }
  .tagline__artist {
    font-family: "Caveat", cursive;
    font-weight: 500;
    font-size: 40px;
    color: var(--label-pink);
  }
  .contact {
    position: absolute;
    top: 576px;
    left: 0;
    width: 1200px;
    font-size: 25px;
    font-weight: 400;
    color: var(--contact-grey);
    list-style: none;
  }
  .contact__item { position: absolute; white-space: nowrap; }
  .contact__item--phone { left: 122px; }
  .contact__item--email { left: 410px; }
  .contact__item--abn { left: 850px; }
</style>
</head>
<body>
  <main class="card">
    <div class="card__frame"></div>
    <div class="gloss-area" role="img" aria-label="Photo of a lip gloss applicator wand"></div>
    <h1 class="brand-name">Rosa Vantelli</h1>
    <div class="pencil-area" role="img" aria-label="Photo of a black makeup pencil"></div>
    <p class="tagline">
      <span class="tagline__lead">MAKEUP BY</span>
      <span class="tagline__artist">Tara Quimbley</span>
    </p>
    <ul class="contact">
      <li class="contact__item contact__item--phone">Ph: 0412 538 064</li>
      <li class="contact__item contact__item--email">E: rosavantelli@mailzone.example</li>
      <li class="contact__item contact__item--abn">ABN: 58902174635</li>
    </ul>
  </main>
</body>
</html>
```